Modern Verdell Tree Care Website

I need a website for a full service Tree Care company. The company provides tree pruning, tree removal, tree preservation, emergency services, stump grinding, and emergency tree services.

Target Market(s)

Customers that need tree services

Industry/Entity Type

Landscaping, Tree Services

Coding

Coded - Design and coding required

Number of Pages Required

5+ page

Font styles to use
Sans Serif

Requirements
Must have
• Good clean design that showcases the services the company provides.
Nice to have
• Services page; contact form, blog, home page, about page

```html
<!DOCTYPE html>
<html lang="en">
<head>
<meta charset="utf-8">
<title>Verdell Tree Care</title>
<link href="https://fonts.googleapis.com/css2?family=Plus+Jakarta+Sans:wght@400;500;600;700&display=swap" rel="stylesheet">
<style>
:root{
  --green:#8cc63f;
  --green-soft:#e9f4dd;
  --ink:#1b1b1b;
  --muted:#555;
  --line:#cfcfcf;
  --white:#fff;
}
*{margin:0;padding:0;box-sizing:border-box}
html,body{width:1200px;height:3358px;overflow:hidden}
body{position:relative;font-family:"Plus Jakarta Sans",sans-serif;color:var(--ink);background:var(--white)}
.abs{position:absolute}
.brand{display:flex;align-items:center;gap:10px;font-weight:700;font-size:20px;color:var(--ink)}
.brand-mark{width:26px;height:26px;background:var(--green)}
.nav{left:0;top:0;width:1200px;height:64px;border-bottom:1px solid #e5e5e5}
.nav .brand{position:absolute;left:100px;top:18px}
.nav-links{position:absolute;right:100px;top:13px;display:flex;align-items:center;gap:27px;font-size:15px;color:#333}
.nav-links span{display:flex;align-items:center;gap:6px}
.btn{display:inline-flex;align-items:center;justify-content:center;gap:8px;font-weight:600;font-size:15px;border-radius:3px}
.btn-green{background:var(--green);color:var(--white)}
.btn-white{background:var(--white);color:var(--green)}
.nav .btn{width:123px;height:37px}
.hero{left:0;top:64px;width:1200px;height:584px;background:linear-gradient(135deg,#4a4038 0%,#6b5d4c 40%,#3d4a52 70%,#5a6b73 100%)}
.hero h1{position:absolute;left:0;width:1200px;top:84px;text-align:center;color:var(--white);font-weight:600;font-size:36px;line-height:42px}
.hero p{position:absolute;left:0;width:1200px;top:180px;text-align:center;color:var(--white);font-size:16px}
.hero .btn{position:absolute;left:510px;top:228px;width:180px;height:49px}
.dots{position:absolute;left:534px;top:294px;display:flex;gap:4px}
.dots i{width:41px;height:4px;background:rgba(255,255,255,.45);border-radius:2px}
.dots i:first-child{background:var(--white)}
.arrows{position:absolute;left:562px;top:402px;display:flex;gap:22px}
.about{left:108px;top:513px;width:1001px;height:637px;background:var(--green);border-radius:4px;color:var(--white);padding:0 84px}
.eyebrow{font-size:14px;font-weight:600;letter-spacing:6px}
.about .eyebrow{position:absolute;top:70px}
.about p{position:absolute;left:84px;width:840px;font-size:23px;line-height:33.5px;font-weight:400}
.about .p1{top:107px}
.about .p2{top:438px}
.about-photo{position:absolute;left:84px;top:254px;width:833px;height:167px;background:linear-gradient(90deg,#56666a,#7a8a6a 45%,#4f6b3a 75%,#89a070)}
.divider{left:100px;top:1193px;width:1000px;height:1px;background:var(--line)}
.services-title{left:100px;top:1240px;font-size:27px;font-weight:600}
.cards{left:100px;top:1316px;width:1000px;display:grid;grid-template-columns:repeat(3,317px);grid-auto-rows:186px;gap:26px 25px}
.card{background:var(--green-soft);border:2px solid var(--green);border-radius:3px;padding:34px 31px 0}
.card h3{font-size:19px;font-weight:500;margin-bottom:12px}
.card p{font-size:14.5px;line-height:22px;color:#333}
.card.active{background:var(--green);color:var(--white)}
.card.active p{color:var(--white)}
.why-label{left:100px;top:2012px;color:var(--green)}
.why-title{left:100px;top:2040px;width:790px;font-size:28px;line-height:38px;font-weight:500;letter-spacing:-0.4px}
.why-btn{left:921px;top:2056px;width:179px;height:50px}
.features{left:100px;top:2176px;width:436px;list-style:none}
.features li{border-bottom:1px solid var(--line);height:59px;display:flex;align-items:center;font-size:19px;color:#555}
.features li:last-child{border-bottom:none}
.features li.open{height:107px;display:block;padding-top:18px}
.features li.open strong{display:flex;align-items:center;gap:16px;color:var(--green);font-weight:500;font-size:19px}
.features li.open small{display:block;font-size:13.5px;line-height:21px;color:#333;padding-left:37px;margin-top:5px;letter-spacing:-0.2px;width:440px}
.why-photo{left:599px;top:2184px;width:501px;height:427px;border-radius:12px;background:linear-gradient(135deg,#a9c6d8 0%,#6e8f4a 45%,#3f5a2a 80%,#8b6a4a 100%)}
.cta{left:0;top:2662px;width:1200px;height:374px;background:linear-gradient(120deg,#2f4a2a,#4d6a35 45%,#6b4a55 80%,#3a4a30)}
.cta h2{position:absolute;left:0;width:1200px;top:111px;text-align:center;color:var(--white);font-weight:500;font-size:28px;line-height:35px}
.cta p{position:absolute;left:0;width:1200px;top:187px;text-align:center;color:#e6e6e6;font-size:15px}
.cta .btn{position:absolute;left:491px;top:227px;width:217px;height:48px;border-radius:0;font-weight:500;font-size:17px}
.footer-brand{left:100px;top:3108px}
.footer-desc{left:100px;top:3158px;width:410px;font-size:15px;line-height:21px;color:#333}
.copy{left:100px;top:3245px;font-size:15px;color:#444}
.socials{left:100px;top:3281px;display:flex;gap:22px}
.socials i{width:15px;height:15px;border-radius:50%;background:var(--green)}
.links{left:642px;top:3105px;font-size:15px;color:#555}
.links h4,.touch h4{font-size:15px;font-weight:600;color:var(--ink);margin-bottom:26px}
.links li{list-style:none;margin-bottom:14px}
.touch{left:790px;top:3103px;width:310px}
.touch p{font-size:15px;margin-bottom:14px}
.subscribe{display:flex;height:35px}
.subscribe span{flex:0 0 216px;border:1px solid #bbb;border-radius:3px 0 0 3px;font-size:13px;color:#666;display:flex;align-items:center;padding-left:19px}
.subscribe b{flex:1;background:var(--green);color:var(--white);font-size:13px;font-weight:600;display:flex;align-items:center;justify-content:center;border-radius:0 3px 3px 0}
.fine{font-size:11px;line-height:16px;color:#777;margin-top:10px}
</style>
</head>
<body>

<header class="abs nav">
  <div class="brand"><span class="brand-mark"></span>Verdell Tree Care</div>
  <nav class="nav-links">
    <span>Home</span><span>About Us</span>
    <span>Services <svg width="12" height="8" viewBox="0 0 12 8"><path d="M1 1l5 5 5-5" fill="none" stroke="#333" stroke-width="1.8"/></svg></span>
    <span>Blog</span>
    <a class="btn btn-green">Contact Us</a>
  </nav>
</header>

<section class="abs hero" role="img" aria-label="Arborist in helmet cutting fallen tree limbs with a chainsaw">
  <h1>Call VERDELL For All Your<br>Tree Care Needs</h1>
  <p>Serving Marrowfield and surrounding areas</p>
  <a class="btn btn-white">Get Started <svg width="14" height="12" viewBox="0 0 14 12"><path d="M1 6h11M7 1l5 5-5 5" fill="none" stroke="currentColor" stroke-width="1.8"/></svg></a>
  <div class="dots"><i></i><i></i><i></i></div>
  <div class="arrows">
    <svg width="24" height="20" viewBox="0 0 24 20"><path d="M23 10H2M10 2l-8 8 8 8" fill="none" stroke="#fff" stroke-width="2.4"/></svg>
    <svg width="24" height="20" viewBox="0 0 24 20"><path d="M1 10h21M14 2l8 8-8 8" fill="none" stroke="#fff" stroke-width="2.4"/></svg>
  </div>
</section>

<section class="abs about">
  <div class="eyebrow">WHO WE ARE</div>
  <p class="p1">At Verdell Tree Care, we are more than just a tree service company, we are stewards to our beautiful trees. With a passion deeply rooted in arboriculture, we are embark on a mission to promote the health, beauty, and safety of your trees and landscapes.</p>
  <div class="about-photo" role="img" aria-label="Crew in safety gear working with chainsaws on a lawn"></div>
  <p class="p2">Whether it’s expert tree trimming to enhance aesthetics, meticulous tree removal to mitigate hazards, or comprehensive tree health assesment to ensure safety, we approach each task with unwavering dedication and attention to detail.</p>
</section>

<div class="abs divider"></div>
<h2 class="abs services-title">Comprehensive Tree Care Solutions</h2>

<div class="abs cards">
  <div class="card active"><h3>Tree Trimming</h3><p>Tree trimming, also known as tree pruning, is the selective removal of branches to enhance the health, appearance, and safety of trees.</p></div>
  <div class="card"><h3>Tree Removal</h3><p>Tree removal, also known as tree felling, is the process of cutting down and removing a tree from its location.</p></div>
  <div class="card"><h3>Tree Clearing</h3><p>ree clearing is the process of permanently removing trees, shrubs, and other vegetation from a specific area</p></div>
  <div class="card"><h3>Tree Pruning</h3><p>Tree pruning, also known as tree trimming, is the selective removal of branches from trees to enhance their health, appearance, &nbsp;safety.</p></div>
  <div class="card"><h3>Tree Grinding</h3><p>Also known as stump removal, is the process of eliminating tree stumps and roots using a specialized machine called a stump grinder.</p></div>
  <div class="card"><h3>Tree Preservation</h3><p>Tree preservation is the practice of protecting trees from damage or removal.</p></div>
  <div class="card"><h3>Storm Damage Cleanup</h3><p>Involves restoring properties that have been affected by severe weather events such as hurricanes, tornadoes, floods, and ice storms.</p></div>
  <div class="card"><h3>Emergency Tree Services</h3><p>Emergency tree services are crucial for addressing immediate or potential threats posed by trees on your property.</p></div>
  <div class="card"><h3>Cabling &amp; Bracing</h3><p>Cabling and bracing are arboricul tural techniques used to support and stabilize trees.</p></div>
</div>

<div class="abs eyebrow why-label">WHY CHOOSE US</div>
<h2 class="abs why-title">Entrusting the care of your trees to experienced<br>professionals is crucial for ensuring their health, safety,<br>and the well-being of your property.</h2>
<a class="abs btn btn-green why-btn">Get Started <svg width="14" height="12" viewBox="0 0 14 12"><path d="M1 6h11M7 1l5 5-5 5" fill="none" stroke="currentColor" stroke-width="1.8"/></svg></a>

<ul class="abs features">
  <li>Licensed and insured</li>
  <li>24- hours emergency services</li>
  <li>Locally owned &amp; operated</li>
  <li class="open"><strong><svg width="20" height="14" viewBox="0 0 20 14"><path d="M2 7h15M11 1l6 6-6 6" fill="none" stroke="#8cc63f" stroke-width="1.8"/></svg>Professional work</strong><small>Professional tree cutters possess in-depth knowledge of<br>tree biology, arboriculture practices, and safety protocols.</small></li>
  <li>Safety is our no.1 priority</li>
  <li>Free estimates</li>
  <li>Licensed arborist on staff</li>
</ul>
<div class="abs why-photo" role="img" aria-label="Worker in protective gear cutting a tree stump with a chainsaw beside a truck"></div>

<section class="abs cta" role="img" aria-label="Family planting a young tree in a garden">
  <h2>Need Expert Tree Care?<br>Contact Us Today!</h2>
  <p>Protect Your Trees, Your Property, and Your Peace of Mind</p>
  <a class="btn btn-white">Talk to an Expert</a>
</section>

<footer>
  <div class="abs brand footer-brand"><span class="brand-mark"></span>Verdell Tree Care</div>
  <p class="abs footer-desc">Full service Tree Care company. The company provides tree pruning, tree removal, tree preservation, emergency services, stump grinding, and emergency tree services</p>
  <p class="abs copy">© 2024 Norvale Consulting All Rights Reserved.</p>
  <div class="abs socials" aria-label="Social links"><i></i><i></i><i></i><i></i></div>
  <div class="abs links"><h4>Links</h4><ul><li>About Us</li><li>Services</li><li>Blog</li></ul></div>
  <div class="abs touch">
    <h4>Get In Touch</h4>
    <p>Join our mailing list for the &nbsp;new updates</p>
    <div class="subscribe"><span>Enter email address</span><b>Subsribe</b></div>
    <p class="fine">By subscribing you agree to our Privacy Policy and<br>consent to receive updates</p>
  </div>
</footer>

</body>
</html>
```